Design a business card
Business name: Harbourline Growth Advisory
Improving Business Profitibility

- An Overview of the Business & Service:

Business Performance Consulting

- The Target Market: Small to medium-sized business

- Design Specifics:
White card, blue ink, moon eclipse

No Logo

Target Market(s)

Small to medium-sized business

Font styles to use
Sans Serif

```html
<!DOCTYPE html>
<html lang="en">
<head>
<meta charset="utf-8">
<title>Harbourline Growth Advisory – Business Card</title>
<link rel="stylesheet" href="https://fonts.googleapis.com/css2?family=Oswald:wght@500&family=Open+Sans:wght@400;600&display=swap">
<style>
  :root {
    --backdrop: #1a1a1a;
    --card-white: #f3f3f3;
    --ink-blue: #04468e;
    --text-dark: #2a2a2a;
    --white: #ffffff;
  }
  * { margin: 0; padding: 0; box-sizing: border-box; }
  html, body { width: 1200px; height: 900px; overflow: hidden; }
  body {
    background: var(--backdrop);
    position: relative;
    font-family: "Open Sans", Arial, sans-serif;
  }
  .card {
    position: absolute;
    top: 200px;
    width: 310px;
    height: 502px;
    box-shadow: 3px 4px 6px rgba(0,0,0,0.55);
  }
  .card-front {
    left: 253px;
    background: var(--card-white);
    border-radius: 62px 0 62px 0;
  }
  .card-back {
    left: 627px;
    background: var(--ink-blue);
    border-radius: 0 62px 0 62px;
  }
  .front-mark {
    position: absolute;
    left: 108px;
    top: 76px;
  }
  .company-name {
    position: absolute;
    left: 0;
    top: 184px;
    width: 100%;
    text-align: center;
    font-family: "Oswald", "Arial Narrow", sans-serif;
    font-weight: 500;
    color: var(--ink-blue);
    text-transform: uppercase;
  }
  .company-name .line-main { display: block; font-size: 27px; line-height: 32px; letter-spacing: 0.2px; }
  .company-name .line-sub { display: block; font-size: 15px; line-height: 20px; letter-spacing: 3.6px; }
  .contact-block {
    position: absolute;
    left: 33px;
    top: 292px;
    color: var(--text-dark);
  }
  .person-name {
    font-family: "Oswald", "Arial Narrow", sans-serif;
    font-weight: 500;
    font-size: 19px;
    line-height: 24px;
    color: var(--ink-blue);
    text-transform: uppercase;
  }
  .person-role { font-size: 14px; line-height: 20px; margin-bottom: 8px; }
  .contact-list { list-style: none; }
  .contact-list li {
    display: flex;
    align-items: center;
    font-size: 14px;
    line-height: 18px;
  }
  .contact-list svg { width: 12px; height: 12px; margin-right: 6px; fill: var(--ink-blue); flex: none; }
  .address { font-size: 14px; line-height: 18px; margin-top: 10px; }
  .back-mark {
    position: absolute;
    left: 75px;
    top: 165px;
  }
  .back-name {
    position: absolute;
    left: 0;
    top: 340px;
    width: 100%;
    text-align: center;
    font-family: "Open Sans", Arial, sans-serif;
    font-weight: 600;
    font-size: 18px;
    letter-spacing: 1px;
    color: var(--white);
  }
  .tagline {
    position: absolute;
    left: 0;
    top: 436px;
    width: 100%;
    text-align: center;
    font-size: 13.5px;
    font-weight: 600;
    letter-spacing: 0.9px;
    color: var(--white);
    text-transform: uppercase;
  }
</style>
</head>
<body>
  <section class="card card-front" aria-label="Card front">
    <svg class="front-mark" width="96" height="96" viewBox="0 0 96 96" aria-hidden="true">
      <circle cx="48" cy="48" r="40" fill="none" stroke="var(--ink-blue)" stroke-width="10"/>
    </svg>
    <h1 class="company-name">
      <span class="line-main">Harbourline Growth</span>
      <span class="line-sub">Advisory</span>
    </h1>
    <div class="contact-block">
      <p class="person-name">Desmond R Akerly</p>
      <p class="person-role">Managing Director</p>
      <ul class="contact-list">
        <li><svg viewBox="0 0 12 12"><path d="M1 4c0-2 2-3 5-3s5 1 5 3l-2 1-1-2H4L3 5zM2 6h8v5H2z"/></svg>044-555 210 468</li>
        <li><svg viewBox="0 0 12 12"><path d="M3 0h6v12H3zM4 1.5v8h4v-8z"/></svg>044-555 210 469</li>
        <li><svg viewBox="0 0 12 12"><path d="M0 2h12v8H0zM1 3l5 4 5-4z" fill-rule="evenodd"/></svg>hello@harbourline.com</li>
        <li><svg viewBox="0 0 12 12"><circle cx="6" cy="6" r="5.5"/></svg>www.harbourline.com</li>
      </ul>
      <p class="address">48 Quayside Row, Suite 5<br>Port Aldwyn, 204871.</p>
    </div>
  </section>

  <section class="card card-back" aria-label="Card back">
    <svg class="back-mark" width="160" height="160" viewBox="0 0 160 160" aria-hidden="true">
      <circle cx="80" cy="80" r="66" fill="none" stroke="var(--white)" stroke-width="14"/>
    </svg>
    <p class="back-name">Harbourline Growth Advisory</p>
    <p class="tagline">Improving Business Profitibility</p>
  </section>
</body>
</html>
```